CM Candle Tube Packaging Design

Website: www.corvelmare.example
IG: @corvel.mare
Tagline: Elevate Your Ambiance
My brand is a sophisticated brand with luxury candles made of coconut wax. Im looking for an upscale minimalist chic design.
Discover the transformative power of positive energy with Corvel Mare candles. Indulge in true luxury with our specially crafted coconut wax blend that not only ignites captivating scents but also embodies modern elegance and empowering elements.
At Corvel Mare we're committed to delivering a unique and exhilarating aromatic experience to all candle lovers. Each candle is meticulously handcrafted in small batches using luxury fragrance oils exclusively formulated for coconut wax.
Our candles are:
Clean-burning
Paraben-Free
Phthalate-Free
Skin-Safe
Pet-Friendly

```html
<!DOCTYPE html>
<html lang="en">
<head>
<meta charset="UTF-8">
<title>Corvel Mare – Candle Label</title>
<link rel="stylesheet" href="https://fonts.googleapis.com/css2?family=Allura&family=Cormorant+Garamond:wght@400&family=Jost:wght@300;400&display=swap">
<style>
  :root {
    --backdrop: #bfb6b0;
    --label-black: #000000;
    --ivory: #f4f1ec;
    --copper: #c98b63;
    --sage: #9aa57f;
    --taupe: #a88b78;
    --rule: #3a3a36;
  }
  * { margin: 0; padding: 0; box-sizing: border-box; }
  html, body { width: 1200px; height: 2400px; overflow: hidden; }
  body { background: var(--backdrop); position: relative; font-family: 'Jost', sans-serif; }

  .label {
    position: absolute; left: 100px; top: 385px;
    width: 1000px; height: 1630px;
    background: var(--label-black);
  }
  .label > * { position: absolute; left: 0; right: 0; text-align: center; line-height: 1; }

  .frame { top: 0; left: 0; width: 1000px; height: 1630px; }

  .brand-name {
    top: 340px;
    font-family: 'Cormorant Garamond', serif; font-weight: 400;
    font-size: 78px; letter-spacing: 2px; color: var(--ivory);
  }
  .brand-line {
    top: 440px; font-weight: 400;
    font-size: 23px; letter-spacing: 9px; color: var(--ivory);
  }
  .brand-note {
    top: 480px;
    font-family: 'Allura', cursive; font-size: 28px; color: var(--ivory);
  }

  .tagline-script {
    top: 555px; left: -40px;
    font-family: 'Allura', cursive; font-size: 220px; color: var(--copper);
  }
  .tagline-your {
    top: 720px; left: -20px;
    font-weight: 300; font-size: 104px; letter-spacing: 2px; color: var(--copper);
  }
  .tagline-main {
    top: 808px;
    font-weight: 300; font-size: 114px; letter-spacing: 3px; color: var(--sage);
  }

  .benefits { top: 1000px; left: 159px; right: 156px; list-style: none; }
  .benefits li {
    height: 62.5px; display: flex; align-items: center; justify-content: center;
    font-weight: 400; font-size: 30px; letter-spacing: 11px; color: var(--taupe);
    border-bottom: 1px solid var(--rule);
  }
  .benefits li:last-child { border-bottom: none; }

  .product-type {
    top: 1405px; font-weight: 400;
    font-size: 28px; letter-spacing: 5px; color: var(--ivory);
  }
  .product-weight {
    top: 1455px; font-weight: 400;
    font-size: 28px; letter-spacing: 1px; color: var(--ivory);
  }
</style>
</head>
<body>
  <section class="label">
    <svg class="frame" viewBox="0 0 1000 1630" aria-hidden="true">
      <g stroke="var(--ivory)" stroke-width="1.5" fill="none">
        <polyline points="295,592 108,592 108,1420 250,1420"/>
        <polyline points="717,592 894,592 894,1420 749,1420"/>
      </g>
      <g stroke="var(--ivory)" stroke-width="2">
        <line x1="260" y1="453" x2="293" y2="453"/>
        <line x1="707" y1="453" x2="740" y2="453"/>
      </g>
    </svg>

    <h1 class="brand-name">CORVEL MARE</h1>
    <p class="brand-line">HANDMADE CANDLES</p>
    <p class="brand-note">with purpose and love</p>

    <p class="tagline-script">Elevate</p>
    <p class="tagline-your">YOUR</p>
    <h2 class="tagline-main">AMBIANCE</h2>

    <ul class="benefits">
      <li>CLEAN-BURNING</li>
      <li>PARABEN-FREE</li>
      <li>PHTHALATE-FREE</li>
      <li>SKIN-SAFE</li>
      <li>PET-FRIENDLY</li>
    </ul>

    <p class="product-type">COCONUT WAX CANDLE</p>
    <p class="product-weight">14OZ. (396G)</p>
  </section>
</body>
</html>
```